900mm double sided Card Ponytail Insert for hair

I need print ready file designs for card packaging inserts for my line of ponytails, These are two sided colour and fold at each end or contain the hair, for structure and so the brand is on display. These will be marketed as luxury ponytails, so we want a simple, soft but luxurious design feel. All the details are below but it will be the logo, photos and simple messaging

Target Market(s)

18-30 females

Industry/Entity Type

Beauty

Font styles to use
Serif

Requirements
Must have
• - Velmora Logo on the back and top front fold.
'Luxury Synthetic Ponytails' Head line
'For effortlessly long and luxurious hair' tag line
'For tutorials, questions and inspiration head to our 'Glow Corner' on velmorabeauty.com'
www.velmorabeauty.com
Tag us on socials! @velmorabeautyofficial (instagram and Facebook logos)
3 step-by-step pictures (holding pictures please until i have some taken)
Nice to have
• (notes to designers) view our website to see our branding velmorabeauty.com - it would be good to use our brand colours and somekind of tropical leaves maybe? i'm thinking palm leaves?
- my brand font is Sweet Getaway - but this may only be good for the biggest headings

```html
<!DOCTYPE html>
<html lang="en">
<head>
<meta charset="utf-8">
<title>Velmora Beauty – Ponytail Card Insert</title>
<link rel="stylesheet" href="https://fonts.googleapis.com/css2?family=Italiana&family=Bodoni+Moda:wght@400&family=Open+Sans:wght@400;600&family=Montserrat:wght@400&display=swap">
<style>
  :root{
    --board:#000;
    --coral:#e0776f;
    --salmon:#f29a80;
    --peach:#f8d8c1;
    --cream:#fdf7f2;
    --gold:#cf9434;
    --text-coral:#e27a70;
    --teal:#5bb5a0;
    --pink:#e0167c;
    --label:#ffffff;
    --inner:#f4f0ec;
    --photo-a:#8d6f5e;
    --photo-b:#c9a680;
    --rule:#ec9a86;
  }
  *{box-sizing:border-box;margin:0;padding:0}
  html,body{width:886px;height:1200px;overflow:hidden;background:var(--board)}
  .board{position:relative;width:886px;height:1200px;background:var(--board)}

  .label{position:absolute;color:var(--label);font:400 12px/1 "Montserrat",sans-serif;letter-spacing:.6px;text-align:center;width:140px}

  .panel{position:absolute;width:122px;overflow:hidden}
  .panel svg.bg{position:absolute;left:0;top:0;width:100%;height:100%}

  /* outer side */
  .outer{height:821px;background:linear-gradient(180deg,var(--cream),#fdf1e9 50%,var(--cream))}
  .wave{position:absolute;left:0;width:122px}
  .wave--top{top:0;height:70px}
  .wave--bottom{bottom:0;height:74px}
  .brand-name{position:absolute;left:0;width:100%;text-align:center;font:400 21px/1 "Italiana",serif;color:var(--gold)}
  .brand-leaf{position:absolute;left:50%;width:40px;height:26px;margin-left:-16px;border-radius:50%;background:radial-gradient(circle at 60% 40%,#f0a2b8 0 18%,#9fd6c7 20%,rgba(159,214,199,0) 72%)}
  .headline{position:absolute;left:0;width:100%;text-align:center;font:400 12px/14px "Italiana",serif;color:#b4614f}
  .divider{position:absolute;left:14px;right:14px;height:1px;background:var(--rule)}
  .divider-mark{position:absolute;left:50%;width:12px;height:12px;margin-left:-6px;border-radius:50%;background:radial-gradient(circle,var(--salmon),rgba(242,154,128,0) 70%)}
  .silhouette{position:absolute;left:28px;width:70px;height:105px;border-radius:45% 50% 40% 45%;background:radial-gradient(ellipse at 45% 45%,#f6cdb0,rgba(248,216,193,.25) 75%)}
  .tagline{position:absolute;left:0;width:100%;text-align:center;font:400 8.6px/10.3px "Bodoni Moda",serif;color:var(--text-coral)}
  .flourish{position:absolute;left:30px;width:64px;height:12px;border-radius:50%;background:linear-gradient(90deg,rgba(200,160,160,0),#d8b6b3,rgba(200,160,160,0))}
  .photo{position:absolute;border-radius:50%;border:2px solid var(--peach);background:radial-gradient(circle at 45% 40%,var(--photo-b),var(--photo-a))}
  .info{position:absolute;left:0;width:100%;text-align:center;font:400 5.9px/8.6px "Open Sans",sans-serif;color:var(--teal)}
  .info .url{font-weight:600;color:var(--pink)}
  .social-dot{position:absolute;left:50%;width:10px;height:10px;margin-left:-5px;border-radius:50%;background:var(--text-coral)}
  .social{position:absolute;left:0;width:100%;text-align:center;font:400 5.9px/8.4px "Open Sans",sans-serif;color:var(--teal)}
  .social .handle{color:#4a3a36;font-weight:600}
  .floral{position:absolute;left:38px;width:46px;height:50px;border-radius:40%;background:radial-gradient(ellipse,#f6c6b4,rgba(246,198,180,0) 70%)}

  /* folds */
  .fold-top{height:194px}
  .fold-top .brand-leaf{top:48px}
  .fold-bottom{height:104px}
  .fold-rule{position:absolute;left:14px;right:14px;height:1px;background:var(--gold)}
  .fold-url{position:absolute;left:0;width:100%;text-align:center;font:600 5.9px/1 "Open Sans",sans-serif;color:var(--pink)}
  .swirl{position:absolute;left:48px;width:26px;height:10px;border-radius:50%;border-bottom:1px solid var(--gold)}

  /* inner */
  .inner{height:821px;background:linear-gradient(180deg,var(--inner),#f0ebe5,var(--inner))}

  .flip{transform:rotate(180deg)}
  .seam{position:absolute;left:0;width:122px;height:1px;background:rgba(150,70,60,.35)}
</style>
</head>
<body>
<main class="board">

  <div class="label" style="left:60px;top:192px">OUTER SIDE</div>
  <div class="label" style="left:204px;top:192px">TOP FOLD</div>
  <div class="label" style="left:351px;top:192px">INNER AREA</div>
  <div class="label" style="left:494px;top:192px">MOCK UP</div>
  <div class="label" style="left:201px;top:564px">BOTTOM FOLD</div>

  <!-- Outer side -->
  <section class="panel outer" style="left:66px;top:215px">
    <svg class="wave wave--top" viewBox="0 0 122 70" preserveAspectRatio="none" aria-hidden="true">
      <path d="M0 0H122V20C95 12 70 22 50 42C35 56 15 62 0 66Z" fill="var(--salmon)"/>
      <path d="M0 0H122V12C100 6 80 16 62 26C40 38 20 44 0 40Z" fill="var(--coral)"/>
    </svg>
    <div class="brand-leaf" style="top:74px" role="img" aria-label="Palm leaf brand motif"></div>
    <div class="brand-name" style="top:102px">Velmora</div>
    <div class="headline" style="top:146px">Luxury<br>Synthetic Ponytails</div>
    <div class="divider-mark" style="top:196px" role="img" aria-label="Small fan ornament"></div>
    <div class="divider" style="top:207px"></div>
    <div class="silhouette" style="top:232px" role="img" aria-label="Illustration of a woman's profile with flowing hair"></div>
    <div class="tagline" style="top:356px">For<br>effortlessly long<br>and<br>luxurious hair</div>
    <div class="flourish" style="top:418px" role="img" aria-label="Scroll ornament"></div>
    <div class="photo" style="left:11px;top:451px;width:52px;height:52px" role="img" aria-label="Model with long dark hair"></div>
    <div class="photo" style="left:57px;top:483px;width:60px;height:60px" role="img" aria-label="Model with wavy blonde hair"></div>
    <div class="photo" style="left:10px;top:508px;width:44px;height:44px" role="img" aria-label="Styled ponytail from the side"></div>
    <div class="photo" style="left:43px;top:546px;width:50px;height:50px" role="img" aria-label="Before and after hair comparison"></div>
    <p class="info" style="top:610px">For tutorials,<br>questions and inspiration<br>head to our<br>‘Glow Corner’ on<br><span class="url">www.velmorabeauty.com</span></p>
    <div class="social-dot" style="top:681px"></div>
    <p class="social" style="top:697px">Tag us on socials!<br><span class="handle">@velmorabeautyofficial</span></p>
    <div class="floral" style="top:722px" role="img" aria-label="Faint floral ornament"></div>
    <svg class="wave wave--bottom" viewBox="0 0 122 74" preserveAspectRatio="none" aria-hidden="true">
      <path d="M0 46C25 40 45 26 70 20C90 14 108 8 122 0V74H0Z" fill="var(--salmon)"/>
      <path d="M0 50C30 58 60 50 85 40C100 34 112 30 122 32V74H0Z" fill="var(--coral)"/>
    </svg>
  </section>

  <!-- Top fold -->
  <section class="panel fold-top" style="left:213px;top:214px">
    <svg class="bg" viewBox="0 0 122 194" preserveAspectRatio="none" aria-hidden="true">
      <defs>
        <radialGradient id="peachGlow" cx="50%" cy="55%" r="65%">
          <stop offset="0" stop-color="#fdf3ea"/><stop offset="1" stop-color="var(--peach)"/>
        </radialGradient>
      </defs>
      <path d="M0 0H122V186C110 194 95 197 82 194C55 186 30 166 0 169Z" fill="url(#peachGlow)"/>
      <path d="M0 0H122V30C100 22 78 30 60 46C40 64 18 70 0 64Z" fill="var(--salmon)"/>
      <path d="M0 0H122V12C100 8 80 18 60 28C40 38 20 44 0 42Z" fill="var(--coral)"/>
    </svg>
    <div class="brand-leaf"></div>
    <div class="brand-name" style="top:82px">Velmora</div>
    <div class="headline" style="top:119px;font-size:11px;line-height:13px">Luxury<br>Synthetic Ponytails</div>
    <div class="fold-rule" style="top:156px"></div>
  </section>

  <!-- Bottom fold -->
  <section class="panel fold-bottom" style="left:213px;top:448px">
    <svg class="bg" viewBox="0 0 122 104" preserveAspectRatio="none" aria-hidden="true">
      <path d="M0 8C15 0 35-2 55 5C80 14 100 26 122 26V104H0Z" fill="url(#peachGlow)"/>
      <path d="M0 84C30 78 55 66 80 54C100 44 112 44 122 46V104H0Z" fill="var(--salmon)"/>
      <path d="M0 90C25 94 55 84 80 74C100 68 112 66 122 68V104H0Z" fill="var(--coral)"/>
    </svg>
    <div class="fold-url" style="top:36px">www.velmorabeauty.com</div>
    <div class="swirl" style="top:44px"></div>
  </section>

  <!-- Inner area -->
  <section class="panel inner" style="left:357px;top:215px" role="img" aria-label="Faint cream floral pattern"></section>

  <!-- Mock up -->
  <section class="panel inner" style="left:503px;top:215px" role="img" aria-label="Faint cream floral pattern"></section>
  <section class="panel fold-top" style="left:503px;top:214px">
    <svg class="bg" viewBox="0 0 122 194" preserveAspectRatio="none" aria-hidden="true">
      <path d="M0 0H122V186C110 194 95 197 82 194C55 186 30 166 0 169Z" fill="url(#peachGlow)"/>
      <path d="M0 0H122V30C100 22 78 30 60 46C40 64 18 70 0 64Z" fill="var(--salmon)"/>
      <path d="M0 0H122V12C100 8 80 18 60 28C40 38 20 44 0 42Z" fill="var(--coral)"/>
    </svg>
    <div class="brand-leaf"></div>
    <div class="brand-name" style="top:82px">Velmora</div>
    <div class="headline" style="top:119px;font-size:11px;line-height:13px">Luxury<br>Synthetic Ponytails</div>
    <div class="fold-rule" style="top:156px"></div>
  </section>
  <section class="panel fold-bottom" style="left:503px;top:932px">
    <svg class="bg" viewBox="0 0 122 104" preserveAspectRatio="none" aria-hidden="true">
      <path d="M0 8C15 0 35-2 55 5C80 14 100 26 122 26V104H0Z" fill="url(#peachGlow)"/>
      <path d="M0 84C30 78 55 66 80 54C100 44 112 44 122 46V104H0Z" fill="var(--salmon)"/>
      <path d="M0 90C25 94 55 84 80 74C100 68 112 66 122 68V104H0Z" fill="var(--coral)"/>
    </svg>
    <div class="fold-url" style="top:36px">www.velmorabeauty.com</div>
    <div class="swirl" style="top:44px"></div>
  </section>

  <!-- Full strip, unfolded -->
  <section class="panel fold-top flip" style="left:690px;top:27px">
    <svg class="bg" viewBox="0 0 122 194" preserveAspectRatio="none" aria-hidden="true">
      <path d="M0 0H122V186C110 194 95 197 82 194C55 186 30 166 0 169Z" fill="url(#peachGlow)"/>
      <path d="M0 0H122V30C100 22 78 30 60 46C40 64 18 70 0 64Z" fill="var(--salmon)"/>
      <path d="M0 0H122V12C100 8 80 18 60 28C40 38 20 44 0 42Z" fill="var(--coral)"/>
    </svg>
    <div class="brand-leaf"></div>
    <div class="brand-name" style="top:82px">Velmora</div>
    <div class="headline" style="top:119px;font-size:11px;line-height:13px">Luxury<br>Synthetic Ponytails</div>
    <div class="fold-rule" style="top:156px"></div>
  </section>
  <div class="seam" style="left:690px;top:221px"></div>

  <section class="panel outer" style="left:690px;top:232px">
    <svg class="wave wave--top" viewBox="0 0 122 70" preserveAspectRatio="none" aria-hidden="true">
      <path d="M0 0H122V20C95 12 70 22 50 42C35 56 15 62 0 66Z" fill="var(--salmon)"/>
      <path d="M0 0H122V12C100 6 80 16 62 26C40 38 20 44 0 40Z" fill="var(--coral)"/>
    </svg>
    <div class="brand-leaf" style="top:74px" role="img" aria-label="Palm leaf brand motif"></div>
    <div class="brand-name" style="top:102px">Velmora</div>
    <div class="headline" style="top:146px">Luxury<br>Synthetic Ponytails</div>
    <div class="divider-mark" style="top:196px" role="img" aria-label="Small fan ornament"></div>
    <div class="divider" style="top:207px"></div>
    <div class="silhouette" style="top:232px" role="img" aria-label="Illustration of a woman's profile with flowing hair"></div>
    <div class="tagline" style="top:356px">For<br>effortlessly long<br>and<br>luxurious hair</div>
    <div class="flourish" style="top:418px" role="img" aria-label="Scroll ornament"></div>
    <div class="photo" style="left:11px;top:451px;width:52px;height:52px" role="img" aria-label="Model with long dark hair"></div>
    <div class="photo" style="left:57px;top:483px;width:60px;height:60px" role="img" aria-label="Model with wavy blonde hair"></div>
    <div class="photo" style="left:10px;top:508px;width:44px;height:44px" role="img" aria-label="Styled ponytail from the side"></div>
    <div class="photo" style="left:43px;top:546px;width:50px;height:50px" role="img" aria-label="Before and after hair comparison"></div>
    <p class="info" style="top:610px">For tutorials,<br>questions and inspiration<br>head to our<br>‘Glow Corner’ on<br><span class="url">www.velmorabeauty.com</span></p>
    <div class="social-dot" style="top:681px"></div>
    <p class="social" style="top:697px">Tag us on socials!<br><span class="handle">@velmorabeautyofficial</span></p>
    <div class="floral" style="top:722px" role="img" aria-label="Faint floral ornament"></div>
    <svg class="wave wave--bottom" viewBox="0 0 122 74" preserveAspectRatio="none" aria-hidden="true">
      <path d="M0 46C25 40 45 26 70 20C90 14 108 8 122 0V74H0Z" fill="var(--salmon)"/>
      <path d="M0 50C30 58 60 50 85 40C100 34 112 30 122 32V74H0Z" fill="var(--coral)"/>
    </svg>
  </section>

  <div class="seam" style="left:690px;top:1068px"></div>
  <section class="panel fold-bottom flip" style="left:690px;top:1069px">
    <svg class="bg" viewBox="0 0 122 104" preserveAspectRatio="none" aria-hidden="true">
      <path d="M0 8C15 0 35-2 55 5C80 14 100 26 122 26V104H0Z" fill="url(#peachGlow)"/>
      <path d="M0 84C30 78 55 66 80 54C100 44 112 44 122 46V104H0Z" fill="var(--salmon)"/>
      <path d="M0 90C25 94 55 84 80 74C100 68 112 66 122 68V104H0Z" fill="var(--coral)"/>
    </svg>
    <div class="fold-url" style="top:36px">www.velmorabeauty.com</div>
    <div class="swirl" style="top:44px"></div>
  </section>

</main>
</body>
</html>
```